Business Card Design for Marketing Firm

Looking for business card design for higher end marketing firm. Clean but impressionable/trendy. We are a marketing firm that represents manufacturers in the foodservice equipment and supply industry. Our customers are end users such has hotels, restaurants, country clubs, convention centers and casinos as well as distributors of restaurants supplies and equipment, and manufacturers of foodservice equipment and supplies.
Target Market(s)
Hotels, Restaurants, Supply & Equipment Distributors, Foodservice Manufacturers
Industry/Entity Type
Foodservice/Hospitality
Contact Information for Business Card
Name, Title, Contact Number, Email, Website, Social Media, Address
Requirements
Must have
- Clean & Simple but Serious and Impressionable

```html
<!DOCTYPE html>
<html lang="en">
<head>
<meta charset="utf-8">
<title>Meridian Foodservice Partners — Business Card</title>
<link rel="stylesheet" href="https://fonts.googleapis.com/css2?family=Lato:wght@400;700&family=Montserrat:wght@400;800&display=swap">
<style>
  :root {
    --navy: #06067c;
    --white: #ffffff;
    --ink-grey: #555a66;
    --rule-grey: #8a8d96;
    --backdrop: #2b2d31;
  }
  * { box-sizing: border-box; margin: 0; padding: 0; }
  html, body { width: 1200px; height: 952px; overflow: hidden; }
  body {
    background: var(--backdrop);
    display: flex;
    flex-direction: column;
    align-items: center;
    justify-content: center;
    gap: 64px;
    font-family: "Lato", sans-serif;
  }
  .card {
    position: relative;
    width: 560px;
    height: 320px;
    border-radius: 22px;
    overflow: hidden;
    box-shadow: 0 14px 30px rgba(0,0,0,.35);
  }

  /* Front side */
  .card-front { background: var(--white); }
  .holder { position: absolute; left: 44px; top: 40px; }
  .holder-name {
    font-family: "Montserrat", sans-serif;
    font-size: 24px;
    letter-spacing: .5px;
    color: var(--navy);
    text-transform: uppercase;
    font-weight: 400;
  }
  .holder-name strong { font-weight: 800; }
  .holder-title {
    font-size: 15px;
    color: var(--ink-grey);
    margin-top: 4px;
  }
  .holder-rule {
    width: 46px;
    height: 2px;
    background: var(--rule-grey);
    margin-top: 10px;
  }
  .contact-item {
    display: flex;
    align-items: flex-start;
    gap: 10px;
    font-size: 12.5px;
    line-height: 1.4;
  }
  .contact-item svg { width: 14px; height: 14px; flex: none; margin-top: 2px; }
  .address {
    position: absolute;
    left: 44px;
    top: 142px;
    color: var(--ink-grey);
  }
  .address svg { fill: var(--navy); }
  .contact-band {
    position: absolute;
    left: 0;
    top: 186px;
    width: 430px;
    height: 110px;
    background: var(--navy);
    clip-path: polygon(0 0, 100% 0, 82% 100%, 0 100%);
    padding: 16px 0 0 44px;
    display: flex;
    flex-direction: column;
    gap: 8px;
    color: var(--white);
  }
  .contact-band svg { fill: var(--white); }

  /* Back side */
  .card-back {
    background: var(--navy);
    display: flex;
    align-items: center;
    justify-content: center;
  }
  .wordmark {
    display: flex;
    align-items: center;
    gap: 14px;
    color: var(--white);
  }
  .wordmark-dot {
    width: 14px; height: 14px; border-radius: 50%;
    background: var(--white);
    flex: none;
  }
  .wordmark-name {
    font-family: "Lato", sans-serif;
    font-weight: 400;
    font-size: 22px;
    letter-spacing: 2px;
    text-transform: uppercase;
    white-space: nowrap;
  }
</style>
</head>
<body>

  <section class="card card-front" aria-label="Card front">
    <div class="holder">
      <h1 class="holder-name">Daniel R. <strong>Whitmore</strong></h1>
      <p class="holder-title">Managing Director</p>
      <div class="holder-rule"></div>
    </div>

    <div class="contact-item address">
      <svg viewBox="0 0 16 16" aria-hidden="true"><path d="M8 1a5 5 0 0 0-5 5c0 3.6 5 9 5 9s5-5.4 5-9a5 5 0 0 0-5-5zm0 7a2 2 0 1 1 0-4 2 2 0 0 1 0 4z"/></svg>
      <span>2140 Lakeview Avenue<br>Portland, OR 97205</span>
    </div>

    <div class="contact-band">
      <div class="contact-item">
        <svg viewBox="0 0 16 16" aria-hidden="true"><path d="M3.6 1.5l2.2 2.6-1.3 1.7a9 9 0 0 0 5.7 5.7l1.7-1.3 2.6 2.2-1.3 2.1C7.6 14.3 1.7 8.4 1.5 2.8z"/></svg>
        <span>+00 987 654 32</span>
      </div>
      <div class="contact-item">
        <svg viewBox="0 0 16 16" aria-hidden="true"><path d="M1 3h14v10H1zm1.5 1.5v.3L8 9l5.5-4.2v-.3zM2.5 6.6v4.9h11V6.6L8 10.8z"/></svg>
        <span>hello@meridianpartners.com</span>
      </div>
      <div class="contact-item">
        <svg viewBox="0 0 16 16" aria-hidden="true"><path d="M3 2l10 5-4.2 1.2L11 13l-2 1-2.2-4.8L3 12z"/></svg>
        <span>www.meridianpartners.com</span>
      </div>
    </div>
  </section>

  <section class="card card-back" aria-label="Card back">
    <div class="wordmark">
      <span class="wordmark-dot" aria-hidden="true"></span>
      <p class="wordmark-name">Meridian Foodservice Partners</p>
    </div>
  </section>

</body>
</html>
```